Surgical Device Brochure for New surgical wound care product (Veltrina)

Four page brochure for surgical device (8.5 x 11). The purpose of this flyer is convince hospital adminstrators and surgeons that Veltrina will save hospitals millions of dollars each year while saving lives and improving patient care.

Use the provided text in the attached document which has the main points. the last page should be space for people to take notes and perform their own calculations. On page 3, please highlight the questions we ask which will help them figure out how much money our product will save them. page 1 and 2 should cover the main points in the document, have quotes, and interesting graphics and layout.

Target Market(s)

Hospital Administrators and Surgeons (medical doctors) and financial controllers

Industry/Entity Type

Medical

Font styles to use
Serif

Colors
85abd2
b7a5cd
fbee3e
e667a6

Requirements
Must have
• Four pages, last page has caption at top with space for notes.
• Emphasis on hospital cost control
Nice to have
• Nice graphics of surgeons, surgery centers, emergency rooms, and surgical tools and graphs showing profits going up and costs going down
• dynamic, exciting, high-tech, clean, organized.
Should not have
• too much red. text that is too small.

```html
<!DOCTYPE html>
<html lang="en">
<head>
<meta charset="utf-8">
<title>Veltrina Brochure Spread</title>
<link rel="stylesheet" href="https://fonts.googleapis.com/css2?family=Open+Sans:wght@300;400;600;700&display=swap">
<style>
  :root {
    --backdrop: #e4e4e4;
    --paper: #ffffff;
    --paper-soft: #f3f3f3;
    --teal: #17998b;
    --teal-line: #a9dcd5;
    --ink-grey: #8a8a8a;
    --white: #ffffff;
  }
  * { box-sizing: border-box; margin: 0; padding: 0; }
  html, body {
    width: 1200px; height: 1000px; overflow: hidden;
    background: var(--backdrop);
    font-family: "Open Sans", Arial, sans-serif;
  }
  .spread {
    position: absolute; left: 28px; top: 130px;
    width: 1144px; height: 740px;
    display: flex;
  }
  .page { position: relative; width: 572px; height: 740px; overflow: hidden; }

  /* Notes page */
  .notes-page { background: var(--paper-soft); }
  .calc-header { position: absolute; left: 48px; top: 44px; display: flex; align-items: center; gap: 12px; }
  .calc-icon { width: 38px; height: 38px; }
  .calc-title { font-weight: 700; font-size: 15px; color: var(--teal); letter-spacing: 0.5px; line-height: 1.1; }
  .calc-subtitle { font-weight: 300; font-size: 11px; color: var(--ink-grey); letter-spacing: 0.6px; }
  .notes-label { position: absolute; left: 60px; top: 104px; font-size: 10px; font-weight: 300; color: var(--teal); }
  .note-lines { position: absolute; left: 60px; right: 48px; top: 130px; }
  .note-line { height: 17px; border-bottom: 1px solid var(--teal-line); }
  .notes-brand { position: absolute; left: 0; right: 0; top: 572px; text-align: center; }
  .contact-band {
    position: absolute; left: 0; right: 0; bottom: 0; height: 112px;
    background: var(--teal); color: var(--white);
    text-align: center; padding-top: 30px;
  }
  .contact-heading { font-size: 9px; font-weight: 700; letter-spacing: 0.4px; margin-bottom: 5px; }
  .contact-detail { font-size: 8px; font-weight: 300; line-height: 1.6; }

  /* Brand name: plain text in the body font */
  .brand-name { font-weight: 400; color: var(--teal); line-height: 1; }
  .notes-brand .brand-name { font-size: 20px; }

  /* Cover page */
  .cover-page { background: var(--paper); }
  .cover-brand { position: absolute; left: 0; right: 0; top: 58px; text-align: center; }
  .cover-brand .brand-name { font-size: 34px; }
  .photo-accent { position: absolute; left: 70px; top: 122px; width: 450px; height: 10px; background: var(--teal); }
  .hero-photo {
    position: absolute; left: 52px; top: 130px; width: 468px; height: 270px;
    background: linear-gradient(160deg, #5f8f8a 0%, #2f7f78 40%, #1f6a66 70%, #6aa0b8 100%);
  }
  .facts-panel {
    position: absolute; left: 52px; top: 400px; width: 468px; height: 214px;
    background: var(--teal); color: var(--white);
    padding: 16px 22px; font-size: 10.5px; line-height: 1.45; text-align: justify;
  }
  .facts-panel p + p { margin-top: 8px; }
  .facts-panel strong { font-weight: 700; }
  .cover-web { position: absolute; left: 0; right: 0; top: 690px; text-align: center; font-size: 9px; color: var(--teal); }
</style>
</head>
<body>
  <main class="spread">
    <section class="page notes-page">
      <header class="calc-header">
        <svg class="calc-icon" viewBox="0 0 38 38" aria-hidden="true">
          <rect x="3" y="3" width="20" height="26" rx="2" fill="none" stroke="#17998b" stroke-width="2"/>
          <rect x="7" y="7" width="12" height="5" fill="#17998b"/>
          <g fill="#17998b">
            <rect x="7" y="15" width="3" height="3"/><rect x="11.5" y="15" width="3" height="3"/><rect x="16" y="15" width="3" height="3"/>
            <rect x="7" y="20" width="3" height="3"/><rect x="11.5" y="20" width="3" height="3"/><rect x="16" y="20" width="3" height="3"/>
          </g>
          <circle cx="26" cy="25" r="9" fill="#fff" stroke="#17998b" stroke-width="2"/>
          <text x="26" y="29.5" text-anchor="middle" font-family="Open Sans, sans-serif" font-size="12" font-weight="700" fill="#17998b">$</text>
        </svg>
        <div>
          <div class="calc-title">CALCULATE</div>
          <div class="calc-subtitle">YOUR TOTAL ANNUAL COST</div>
        </div>
      </header>
      <div class="notes-label">Notes :</div>
      <div class="note-lines">
        <div class="note-line"></div><div class="note-line"></div><div class="note-line"></div><div class="note-line"></div>
        <div class="note-line"></div><div class="note-line"></div><div class="note-line"></div><div class="note-line"></div>
        <div class="note-line"></div><div class="note-line"></div><div class="note-line"></div><div class="note-line"></div>
        <div class="note-line"></div><div class="note-line"></div><div class="note-line"></div><div class="note-line"></div>
        <div class="note-line"></div><div class="note-line"></div><div class="note-line"></div><div class="note-line"></div>
        <div class="note-line"></div><div class="note-line"></div><div class="note-line"></div><div class="note-line"></div>
        <div class="note-line"></div>
      </div>
      <div class="notes-brand">
        <div class="brand-name">Veltrina</div>
      </div>
      <footer class="contact-band">
        <div class="contact-heading">FOR PRODUCT INQUIRIES AND PURCHASES, PLEASE CONTACT US:</div>
        <div class="contact-detail">info@veltrinamed.com Product Information &amp; Inquiries | orders@veltrinamed.com | Phone (555) 214-0386</div>
        <div class="contact-detail">www.veltrinaclose.com</div>
      </footer>
    </section>

    <section class="page cover-page">
      <div class="cover-brand">
        <div class="brand-name">Veltrina</div>
      </div>
      <div class="photo-accent"></div>
      <div class="hero-photo" role="img" aria-label="Photo collage of a surgical team in green scrubs operating, with smaller insets of surgical tools and an operating room"></div>
      <div class="facts-panel">
        <p>In 2016, the Federal Government increased Medicare penalties to $528 million, which currently impacts 2,597 hospitals with an average amount of $203,000 per facility. (Dana Whitfield, August 4, 2016, Clinical Cost Review, healthdesk.org)</p>
        <p>Surgical Site Infection costs hospitals between <strong>$11,000</strong> to <strong>$35,000</strong> for each case of infection.</p>
        <p>State Health Quality Board "Surgical Site Infection (SSI) continues to represent a significant portion of healthcare associated infections." - National Health Standards Office.</p>
        <p>Hospitals that reduce their Surgical Site Infection rate stand to <strong>save</strong> an estimated <strong>$1</strong> to <strong>$2 million per year</strong> annual SSI Related Cost savings. - State Health Quality Board</p>
      </div>
      <div class="cover-web">www.veltrinaclose.com</div>
    </section>
  </main>
</body>
</html>
```